Verodex business card

Business card for sustainable investment company called "Verodex". Verodex is an exchange platform selling carbon credits between buyers and sellers. Carbon Credits are an environmental commodity for reducing global carbon emissions.

the card should obviously have our logo and the theme should be sustainability/environment mixed with a trading platform.

Contact Information for Business Card

Logo, Name, Title, Phone, Email

Colors
0054AA
0677BA
7BADD7
CADEEF
E8F1F8
0094D4
00A9DD
6FCCEA
C7EBF8
E9F6FB
00AB8E
00BBA5
67D7C9
C6EFE9
E9F9F6
59FF00
82FF00
B8FF75
E3FFCB
F4FFEA

```html
<!DOCTYPE html>
<html lang="en">
<head>
<meta charset="utf-8">
<title>Verodex business card</title>
<link rel="stylesheet" href="https://fonts.googleapis.com/css2?family=Montserrat:wght@600;700&family=Arimo:wght@400;700&display=swap">
<style>
  :root {
    --stage: #101416;
    --card: #0f2a33;
    --card-deep: #0b2129;
    --edge-sky: #00A9DD;
    --edge-teal: #00BBA5;
    --edge-lime: #82FF00;
    --accent: #00BBA5;
    --accent-soft: #67D7C9;
    --leaf: #59FF00;
    --ink: #E9F9F6;
    --ink-muted: #C6EFE9;
    --rule: #67D7C9;
  }
  * { box-sizing: border-box; margin: 0; padding: 0; }
  html, body { width: 1200px; height: 963px; overflow: hidden; }
  body {
    background: var(--stage);
    display: flex;
    flex-direction: column;
    align-items: center;
    justify-content: center;
    gap: 70px;
    font-family: "Arimo", Arial, sans-serif;
  }
  .card {
    position: relative;
    width: 600px;
    height: 343px;
    border-radius: 22px;
    background: linear-gradient(135deg, var(--card) 0%, var(--card-deep) 100%);
    overflow: hidden;
    box-shadow: 0 18px 40px rgba(0,0,0,.55);
  }
  .card::after {
    content: "";
    position: absolute;
    inset: 0;
    border-radius: 22px;
    padding: 0 3px 3px 0;
    background: linear-gradient(90deg, var(--edge-sky), var(--edge-teal) 55%, var(--edge-lime));
    -webkit-mask: linear-gradient(#000 0 0) content-box, linear-gradient(#000 0 0);
    -webkit-mask-composite: xor;
    mask-composite: exclude;
    pointer-events: none;
  }
  .brand {
    display: flex;
    align-items: center;
    gap: 14px;
  }
  .brand-dot {
    width: 34px;
    height: 34px;
    border-radius: 50%;
    background: var(--leaf);
  }
  .brand-name {
    font-family: "Montserrat", Arial, sans-serif;
    font-weight: 700;
    color: var(--ink);
    letter-spacing: 3px;
  }

  /* front */
  .card-front .brand { position: absolute; left: 48px; top: 132px; }
  .card-front .brand-name { font-size: 30px; }
  .divider {
    position: absolute;
    left: 300px;
    top: 62px;
    width: 1.5px;
    height: 220px;
    background: var(--rule);
  }
  .contact {
    position: absolute;
    left: 326px;
    top: 76px;
    color: var(--ink);
  }
  .person-name {
    font-family: "Montserrat", Arial, sans-serif;
    font-weight: 700;
    font-size: 21px;
    letter-spacing: 1px;
    color: var(--accent);
    text-transform: uppercase;
  }
  .person-title { font-size: 15px; color: var(--ink-muted); margin-top: 2px; }
  .address { font-size: 15px; line-height: 1.35; margin-top: 14px; }
  .lines { list-style: none; margin-top: 14px; }
  .lines li {
    display: flex;
    align-items: center;
    gap: 10px;
    font-size: 15px;
    line-height: 1.65;
  }
  .lines svg { width: 15px; height: 15px; flex: none; }

  /* back */
  .card-back .brand {
    position: absolute;
    left: 50%;
    top: 50%;
    transform: translate(-50%, -50%);
    gap: 20px;
  }
  .card-back .brand-dot { width: 52px; height: 52px; }
  .card-back .brand-name { font-size: 46px; letter-spacing: 4px; }
</style>
</head>
<body>
  <section class="card card-front" aria-label="Card front">
    <div class="brand">
      <span class="brand-dot"></span>
      <span class="brand-name">VERODEX</span>
    </div>
    <div class="divider"></div>
    <div class="contact">
      <p class="person-name">Marcus Hale</p>
      <p class="person-title">Manager</p>
      <p class="address">Your Address, City<br>State, Zip 0000</p>
      <ul class="lines">
        <li>
          <svg viewBox="0 0 16 16" fill="none" stroke="#67D7C9" stroke-width="1.6"><path d="M3 2.5h3l1 3-1.6 1.2a8 8 0 0 0 3.9 3.9L10.5 9l3 1v3a1 1 0 0 1-1 1A11 11 0 0 1 2 3.5a1 1 0 0 1 1-1z"/></svg>
          555-014-2290
        </li>
        <li>
          <svg viewBox="0 0 16 16" fill="none" stroke="#67D7C9" stroke-width="1.4"><rect x="1.5" y="3.5" width="13" height="9" rx="1"/><path d="M1.8 4l6.2 5 6.2-5"/></svg>
          marcus@verodex.com
        </li>
        <li>
          <svg viewBox="0 0 16 16" fill="none" stroke="#67D7C9" stroke-width="1.3"><circle cx="8" cy="8" r="6.3"/><ellipse cx="8" cy="8" rx="2.8" ry="6.3"/><path d="M1.7 8h12.6M2.6 5h10.8M2.6 11h10.8"/></svg>
          www.verodex.com
        </li>
      </ul>
    </div>
  </section>

  <section class="card card-back" aria-label="Card back">
    <div class="brand">
      <span class="brand-dot"></span>
      <span class="brand-name">VERODEX</span>
    </div>
  </section>
</body>
</html>
```